Employee Benefits and Insurance Consulting

We are an existing company with over 30 years experience but are changing our name. We would like a simple design with grey tones.

Industry/Entity Type

Insurance

Contact Information for Business Card

Marlow Benefits Consulting
Gerald P Hollins CEO
5172 Brackenridge Road
Ashbury, TN 37912
gerald@marlowbenefits-example.com
865-412-5593 - O
865-247-3861 - C

```html
<!DOCTYPE html>
<html lang="en">
<head>
<meta charset="utf-8">
<title>Marlow Benefits Consulting – Business Card</title>
<link rel="stylesheet" href="https://fonts.googleapis.com/css2?family=Lato:ital,wght@0,300;0,400;0,700;1,400&display=swap">
<style>
  :root {
    --backdrop: #d9d9d9;
    --card: #f4f5f5;
    --accent-blue: #2a9bd8;
    --band-grey: #8e8f91;
    --text-grey: #6b6c6e;
    --text-dark: #4a4b4d;
    --white: #ffffff;
  }
  * { margin: 0; padding: 0; box-sizing: border-box; }
  html, body {
    width: 1200px;
    height: 900px;
    overflow: hidden;
    background: var(--backdrop);
    font-family: "Lato", Arial, sans-serif;
  }
  .card {
    position: absolute;
    left: 110px;
    top: 170px;
    width: 980px;
    height: 560px;
    background: var(--card);
    box-shadow: 0 6px 24px rgba(0,0,0,0.18);
    overflow: hidden;
  }
  .brand {
    position: absolute;
    right: 60px;
    top: 70px;
    display: flex;
    align-items: center;
    gap: 16px;
  }
  .brand-dot {
    width: 34px;
    height: 34px;
    border-radius: 50%;
    background: var(--accent-blue);
  }
  .brand-name {
    font-size: 34px;
    font-weight: 300;
    color: var(--text-dark);
    letter-spacing: 0.5px;
  }
  .divider {
    position: absolute;
    left: 40px;
    right: 40px;
    top: 300px;
    height: 2px;
    background: var(--accent-blue);
  }
  .person-name {
    position: absolute;
    left: 60px;
    top: 245px;
    font-size: 38px;
    font-weight: 400;
    color: var(--accent-blue);
  }
  .person-title {
    position: absolute;
    left: 62px;
    top: 312px;
    font-size: 17px;
    font-style: italic;
    color: var(--text-grey);
  }
  .phones {
    position: absolute;
    left: 320px;
    top: 330px;
    list-style: none;
  }
  .phones li {
    display: flex;
    align-items: center;
    gap: 12px;
    font-size: 20px;
    color: var(--text-grey);
    height: 36px;
  }
  .phones svg { width: 24px; height: 24px; }
  .address {
    position: absolute;
    left: 630px;
    top: 318px;
    font-size: 18px;
    line-height: 30px;
    color: var(--text-grey);
    font-style: normal;
  }
  .bands {
    position: absolute;
    left: 0;
    bottom: 0;
    width: 980px;
    height: 140px;
  }
  .email {
    position: absolute;
    right: 40px;
    top: 448px;
    font-size: 21px;
    color: var(--white);
    letter-spacing: 0.3px;
  }
</style>
</head>
<body>
  <main class="card">
    <div class="brand">
      <span class="brand-dot"></span>
      <span class="brand-name">Marlow Benefits Consulting</span>
    </div>

    <h1 class="person-name">Gerald P Hollins</h1>
    <div class="divider"></div>
    <p class="person-title">CEO</p>

    <ul class="phones">
      <li>
        <svg viewBox="0 0 24 24" aria-hidden="true">
          <circle cx="12" cy="12" r="10.5" fill="none" stroke="var(--accent-blue)" stroke-width="1.6"/>
          <path d="M8.6 7.2c.4-.3.9-.2 1.1.2l1 1.8c.2.4.1.8-.2 1.1l-.7.6c.6 1.3 1.5 2.2 2.8 2.8l.6-.7c.3-.3.7-.4 1.1-.2l1.8 1c.4.2.5.7.2 1.1l-.7.9c-.5.6-1.3.8-2 .5-2.8-1.1-4.9-3.2-6-6-.3-.7-.1-1.5.5-2z" fill="var(--accent-blue)"/>
        </svg>
        <span>865-247-3861</span>
      </li>
      <li>
        <svg viewBox="0 0 24 24" aria-hidden="true">
          <circle cx="12" cy="12" r="11" fill="var(--accent-blue)"/>
          <path d="M8.6 7.2c.4-.3.9-.2 1.1.2l1 1.8c.2.4.1.8-.2 1.1l-.7.6c.6 1.3 1.5 2.2 2.8 2.8l.6-.7c.3-.3.7-.4 1.1-.2l1.8 1c.4.2.5.7.2 1.1l-.7.9c-.5.6-1.3.8-2 .5-2.8-1.1-4.9-3.2-6-6-.3-.7-.1-1.5.5-2z" fill="var(--white)"/>
        </svg>
        <span>865-412-5593</span>
      </li>
    </ul>

    <address class="address">
      5172 Brackenridge Road<br>
      Ashbury, TN 37912
    </address>

    <svg class="bands" viewBox="0 0 980 140" aria-hidden="true">
      <polygon points="560,0 980,0 980,78 530,78" fill="var(--band-grey)"/>
      <polygon points="0,84 540,84 520,118 0,118" fill="var(--accent-blue)"/>
    </svg>
    <p class="email">gerald@marlowbenefits-example.com</p>
  </main>
</body>
</html>
```